Brookvale Building Company - advertisement poster

I am looking to print some canvas signs to advertise my general contracting company, Brookvale Building Company. The sign will measure 6' long x 3' high so the size should match that ratio. I already have a logo icon, which is the Letter 'B' and some trees that I would like to incorporate, see attached. I would also like the to have the following information listed:
1) phone number: 831-555-0172
2) email: brookvalebuildingcompany@mailnest.example
3) website: brookvalebuildingcompany.example
4) Lic#4826130
5) I want to use this text: "BUILD WITH THE B-CREW!"

The ad should be relatively simple and clean. Black and Green are my company colors. I am open to creative ideas!

Target Market(s)

People looking to renovate their homes

Industry/Entity Type

Construction

Colors
59FF00
82FF00
B8FF75
E3FFCB
F4FFEA

Requirements
Must have
• Must have my company logo
Should not have
• No photos or complex graphics

```html
<!DOCTYPE html>
<html lang="en">
<head>
<meta charset="UTF-8">
<title>Brookvale Building Company – Sign</title>
<link rel="stylesheet" href="https://fonts.googleapis.com/css2?family=Montserrat:wght@500;600;700&family=Syncopate:wght@400;700&display=swap">
<style>
  :root {
    --sign-bg: #e3efc2;
    --page-bg: #d9dde3;
    --navy: #252a6c;
    --green: #6cb63f;
  }
  * { margin: 0; padding: 0; box-sizing: border-box; }
  html, body {
    width: 1200px; height: 800px; overflow: hidden;
    background: var(--page-bg);
  }
  .sign {
    position: absolute; left: 0; top: 100px;
    width: 1200px; height: 600px;
    background: var(--sign-bg);
    color: var(--navy);
    font-family: "Montserrat", sans-serif;
  }
  .brand {
    position: absolute; top: 70px; left: 0; width: 100%;
    display: flex; flex-direction: column; align-items: center; gap: 18px;
  }
  .brand-mark {
    width: 64px; height: 64px; background: var(--green);
  }
  .brand-name {
    font-family: "Montserrat", sans-serif;
    font-weight: 700; font-size: 30px; letter-spacing: 0.02em;
    color: var(--navy);
  }
  .headline {
    position: absolute; top: 228px; left: 0; width: 100%;
    text-align: center; font-family: "Syncopate", sans-serif;
    color: var(--navy); line-height: 1;
  }
  .headline-lead {
    display: block; font-weight: 400; font-size: 46px;
    letter-spacing: 0.02em; padding-left: 120px;
  }
  .headline-main {
    display: block; font-weight: 700; font-size: 118px;
    letter-spacing: 0.06em; margin-top: 14px; padding-left: 40px;
  }
  .contact {
    position: absolute; top: 452px; left: 0; width: 100%; height: 110px;
  }
  .phone {
    position: absolute; left: 86px; top: 0;
    display: flex; flex-direction: column; align-items: center; gap: 14px;
  }
  .phone-pill {
    display: flex; align-items: center; gap: 22px;
    background: var(--green); border-radius: 10px;
    width: 340px; height: 58px; padding: 0 22px;
    font-weight: 700; font-size: 34px; letter-spacing: 0.02em;
  }
  .licence { font-weight: 500; font-size: 17px; }
  .contact-item {
    position: absolute; top: 4px;
    display: flex; flex-direction: column; align-items: flex-start;
  }
  .contact-item.web { left: 490px; }
  .contact-item.mail { left: 820px; }
  .contact-line {
    display: flex; align-items: center; gap: 12px;
    font-weight: 600; font-size: 19px; letter-spacing: 0.02em;
  }
  .contact-tag {
    margin-left: 34px; margin-top: 8px;
    background: var(--green); border-radius: 3px;
    padding: 2px 10px; font-weight: 600; font-size: 15px;
  }
</style>
</head>
<body>
  <main class="sign">
    <header class="brand">
      <div class="brand-mark"></div>
      <div class="brand-name">Brookvale Building Company</div>
    </header>

    <h1 class="headline">
      <span class="headline-lead">BUILD WITH THE</span>
      <span class="headline-main">B-CREW!</span>
    </h1>

    <section class="contact">
      <div class="phone">
        <div class="phone-pill">
          <svg width="26" height="26" viewBox="0 0 24 24" aria-hidden="true">
            <path fill="var(--navy)" d="M6.6 10.8a15.1 15.1 0 0 0 6.6 6.6l2.2-2.2a1 1 0 0 1 1-.25 11.4 11.4 0 0 0 3.6.57 1 1 0 0 1 1 1V20a1 1 0 0 1-1 1A17 17 0 0 1 3 4a1 1 0 0 1 1-1h3.5a1 1 0 0 1 1 1c0 1.25.2 2.45.57 3.57a1 1 0 0 1-.25 1z"/>
          </svg>
          <span>831.555.0172</span>
        </div>
        <div class="licence">License Number: 4826130</div>
      </div>

      <div class="contact-item web">
        <div class="contact-line">
          <svg width="22" height="22" viewBox="0 0 24 24" aria-hidden="true" fill="none" stroke="var(--navy)" stroke-width="2">
            <circle cx="12" cy="12" r="9"/><ellipse cx="12" cy="12" rx="4" ry="9"/><path d="M3 12h18M5 7h14M5 17h14"/>
          </svg>
          <span>BrookvaleBuildingCompany</span>
        </div>
        <span class="contact-tag">.example</span>
      </div>

      <div class="contact-item mail">
        <div class="contact-line">
          <svg width="22" height="18" viewBox="0 0 24 18" aria-hidden="true">
            <rect x="1" y="1" width="22" height="16" fill="var(--navy)"/>
            <path d="M1 1l11 9 11-9" fill="none" stroke="var(--sign-bg)" stroke-width="2"/>
          </svg>
          <span>BrookvaleBuildingCompany</span>
        </div>
        <span class="contact-tag">@mailnest.example</span>
      </div>
    </section>
  </main>
</body>
</html>
```